Professional Single Page Website Design for Tollbrook Advisory

Tollbrook Advisory is a new business consultancy specializing in providing expert services to small businesses, primarily in the brick-and-mortar retail and food service sectors. We offer a range of services including franchise development and launch, due diligence, and construction management.

Currently, we have a basic website set up at www.tollbrookadvisory.example, but we need a professional touch to enhance its design and functionality.

Project Requirements:
- Single Page Design: For now, we need a single page design that effectively showcases who we are, our services, and contact information.
- Future Expansion: The design should be flexible and scalable for future expansion to include additional pages like specific service offerings, about us, and a dedicated contact page.
- Design Aesthetic: We are looking for a modern yet professional design that aligns with our brand identity.
- Logo: We have a logo that we like, which was also sourced from Pixel Bazaar. The logo files are attached to this project brief.

Key Sections to Include:
- Hero Section: An engaging introduction to Tollbrook Advisory with a strong visual impact.
- About Us: A brief overview of who we are and our mission.
- Team: Section for the profiles of the two principals.
- Services: A clear and concise presentation of our services, including franchise development, due diligence, and construction management.
- Contact Information: Easy-to-find contact details, including a form for inquiries.
- Call to Action: Encouraging visitors to get in touch with us for consultations or further information.

Design Considerations:
- Ensure the design is responsive and mobile-friendly.
- Include high-quality images and icons that complement our services and industry.
- We do not need development services, this is only a design project.

```html
<!DOCTYPE html>
<html lang="en">
<head>
<meta charset="utf-8">
<title>Tollbrook Advisory</title>
<link href="https://fonts.googleapis.com/css2?family=Poppins:wght@400;500;600;700&display=swap" rel="stylesheet">
<style>
:root{
  --green:#95c7b0;
  --green-light:#a9d3bf;
  --navy:#1f2631;
  --text:#3a3f47;
  --grey-band:#f1f1f1;
  --white:#ffffff;
}
*{box-sizing:border-box;margin:0;padding:0}
html,body{width:1200px;height:3676px;overflow:hidden}
body{position:relative;font-family:'Poppins',sans-serif;color:var(--text);background:var(--white)}
.abs{position:absolute}
.bg-shape{position:absolute;left:0;top:0;width:1200px;height:3676px}

/* Header */
.brand{position:absolute;display:flex;align-items:center;gap:12px;font-weight:600;font-size:22px;color:var(--white);line-height:1}
.brand-dot{width:34px;height:34px;border-radius:50%;background:var(--green)}
.nav{position:absolute;left:473px;top:68px;display:flex;gap:40px;font-size:15px;font-weight:500;color:var(--white)}
.nav .active{color:var(--green);text-decoration:underline;text-underline-offset:5px}
.btn{display:inline-flex;align-items:center;justify-content:center;border-radius:30px;font-weight:600;font-family:'Poppins',sans-serif}
.btn-green{background:var(--green);color:var(--navy)}
.header-cta{position:absolute;left:920px;top:56px;width:206px;height:46px;font-size:16px}

/* Hero */
.hero-copy{position:absolute;left:150px;top:200px;width:900px;text-align:center;color:var(--white)}
.hero-copy h1{font-size:64px;font-weight:700;line-height:60px;letter-spacing:-0.5px}
.hero-copy h2{font-size:25px;font-weight:500;margin-top:10px}
.hero-copy p{font-size:16.5px;line-height:28px;margin:14px auto 0;width:870px}
.hero-btn{position:absolute;left:525px;top:518px;width:152px;height:46px;font-size:16px}

/* Section headings */
.section-title{position:absolute;left:0;width:1200px;text-align:center;font-size:42px;font-weight:700;color:var(--navy)}
.rule{position:absolute;height:3px;width:108px;background:var(--green)}

/* About */
.about-title{left:74px;top:800px;font-size:42px;font-weight:700;color:var(--navy)}
.sub-title{font-size:28px;font-weight:700;color:var(--green)}
.body-copy{font-size:13.5px;line-height:24px;color:var(--text)}
.body-copy+.body-copy{margin-top:8px}
.about-col{position:absolute;left:74px;width:510px}

/* Services */
.tabs{position:absolute;left:227px;top:1613px;display:flex;align-items:center;gap:24px;font-size:19px;font-weight:600;color:var(--navy)}
.tab{padding:0 22px;height:48px;display:flex;align-items:center}
.tab.active{border:2px solid var(--green);border-radius:26px;color:var(--green)}
.service-text{position:absolute;left:614px;top:1742px;width:500px}

/* Team */
.member-text{position:absolute;width:250px}
.member-name{font-size:29px;font-weight:700;color:var(--green)}
.member-role{font-size:18px;font-weight:500;color:var(--navy);margin:4px 0 8px}

/* Contact */
.contact-title{color:var(--white)}
.addr-item{position:absolute;left:131px;width:400px;text-align:center;color:var(--white)}
.addr-heading{top:3100px;font-size:32px;font-weight:700;line-height:48px}
.addr-brand{top:3200px;display:flex;align-items:center;justify-content:center;gap:12px;font-size:26px;font-weight:600;line-height:40px}
.addr-brand .brand-dot{width:40px;height:40px}
.addr-lines{top:3300px;font-size:19px;line-height:30px;font-weight:500}
.addr-link{top:3384px;color:var(--green);font-size:17px;line-height:24px;text-decoration:underline}
.quick-title{position:absolute;left:616px;top:3090px;font-size:35px;font-weight:700;color:var(--navy)}
.field{position:absolute;height:48px;border:1.5px solid #c9cdd2;border-radius:24px;font-size:15px;padding:14px 18px;color:var(--navy)}
.field.msg{height:108px;border-radius:22px}
.submit{position:absolute;left:616px;top:3383px;width:140px;height:49px;background:var(--navy);color:var(--white);font-size:18px}

/* Footer */
.footer-rule{position:absolute;left:74px;top:3610px;width:1126px;height:1px;background:#7fb39b}
.copyright{position:absolute;left:74px;top:3630px;font-size:12px;color:var(--navy)}
.social{position:absolute;left:954px;top:3628px;display:flex;gap:16px}
.social span{width:24px;height:24px;border-radius:50%;background:var(--navy)}
</style>
</head>
<body>

<!-- Background shapes -->
<svg class="bg-shape" viewBox="0 0 1200 3676" aria-hidden="true">
  <defs>
    <linearGradient id="heroGrad" x1="0" y1="0" x2="1" y2="1">
      <stop offset="0" stop-color="#5d6b73"/>
      <stop offset="0.5" stop-color="#6a4a3e"/>
      <stop offset="1" stop-color="#7a3f31"/>
    </linearGradient>
  </defs>
  <path d="M0 1581 C250 1470 420 1405 600 1405 C780 1405 950 1470 1200 1581 L1200 2340 C950 2220 780 2165 600 2165 C420 2165 250 2220 0 2340 Z" fill="var(--grey-band)"/>
  <path d="M0 2948 C250 2840 420 2770 600 2770 C780 2770 950 2840 1200 2948 L1200 3676 L0 3676 Z" fill="var(--green)"/>
</svg>

<!-- Hero -->
<svg class="abs" style="left:0;top:0" width="1200" height="735" role="img" aria-label="Photo of a modern brick commercial building with a parking lot under a cloudy sky">
  <path d="M0 0 H1200 V557 C950 680 780 731 600 731 C420 731 250 680 0 557 Z" fill="url(#heroGrad)"/>
  <path d="M0 0 H1200 V557 C950 680 780 731 600 731 C420 731 250 680 0 557 Z" fill="#000" opacity="0.35"/>
</svg>

<div class="brand" style="left:74px;top:62px"><span class="brand-dot"></span>Tollbrook Advisory</div>
<nav class="nav">
  <span class="active">Home</span><span>About</span><span>Services</span><span>Team</span><span>Contact</span>
</nav>
<a class="btn btn-green header-cta">Get in Touch with us</a>

<div class="hero-copy">
  <h1>Building Success<br>in Southern California</h1>
  <h2>Expertise at Every Step: From Planning to Execution</h2>
  <p>At Tollbrook, we blend innovative strategies with local market expertise to guide your commercial real estate ventures. Whether you're launching a new restaurant, investing in retail spaces, or expanding a franchise, our dedicated team is here to turn your real estate aspirations into tangible success. Dive into a partnership that grows with you.</p>
</div>
<a class="btn btn-green hero-btn">Learn More</a>

<!-- About -->
<h2 class="abs about-title">About Us</h2>
<div class="rule" style="left:74px;top:866px"></div>
<div class="about-col" style="top:905px">
  <h3 class="sub-title">Who we are</h3>
  <p class="body-copy" style="margin-top:4px">Welcome to Tollbrook Advisory, your trusted partner in navigating the complexities of the real estate and small business markets. Founded by industry veterans Rafael Moreno and Evan Park, we specialize in providing comprehensive services tailored to the unique needs of our clients.</p>
  <p class="body-copy">Whether you're a franchisee, a new restaurant owner, or a commercial real estate investor, our expertise in due diligence, construction management, and investment property evaluation ensures you make informed, strategic decisions.</p>
</div>
<div class="about-col" style="top:1173px">
  <h3 class="sub-title">Our Mission</h3>
  <p class="body-copy" style="margin-top:4px">Welcome to Tollbrook Advisory, your trusted partner in navigating the complexities of the real estate and small business markets. Founded by industry veterans Rafael Moreno and Evan Park, we specialize in providing comprehensive services tailored to the unique needs of our clients.</p>
</div>
<svg class="abs" style="left:616px;top:806px" width="512" height="512" role="img" aria-label="Photo of two businessmen in suits looking at a laptop">
  <defs><linearGradient id="aboutGrad" x1="0" y1="0" x2="1" y2="1"><stop offset="0" stop-color="#dfe6ee"/><stop offset="1" stop-color="#1f2a4a"/></linearGradient></defs>
  <rect x="75" y="75" width="362" height="362" rx="44" transform="rotate(45 256 256)" fill="url(#aboutGrad)"/>
</svg>

<!-- Services -->
<h2 class="section-title" style="top:1502px">Our Services</h2>
<div class="rule" style="left:546px;top:1568px"></div>
<div class="tabs">
  <span class="tab active">Franchise Development</span>
  <span class="tab">Due Diligence</span>
  <span class="tab">Construction Management</span>
</div>
<svg class="abs" style="left:64px;top:1762px" width="494" height="294" role="img" aria-label="Illustration of business people presenting a world map on a board">
  <ellipse cx="260" cy="170" rx="240" ry="120" fill="#c8d8ee"/>
  <rect x="0" y="288" width="494" height="3" fill="#a9b6c8"/>
</svg>
<div class="service-text">
  <h3 class="sub-title">Franchise Development</h3>
  <p class="body-copy" style="margin-top:4px">At Tollbrook Advisory, our Franchise Development &amp; Launch service is designed to transform your successful business into a thriving franchise. We start by thoroughly evaluating your business model to determine its franchisability. Once confirmed, our team handles every aspect of the franchise setup, including legal documentation, branding, marketing strategies, operational guidelines, and franchisee recruitment.</p>
  <p class="body-copy">Our goal is to ensure a seamless and efficient transition from a single successful location to a robust franchise network, empowering your business to scale effectively and achieve exponential growth. Partner with us to turn your business into a nationwide brand.</p>
</div>

<!-- Team -->
<h2 class="section-title" style="top:2328px">Our Leadership Team</h2>
<div class="rule" style="left:546px;top:2394px"></div>

<svg class="abs" style="left:74px;top:2433px" width="238" height="238" role="img" aria-label="Portrait photo of Evan Park">
  <rect x="40" y="40" width="158" height="158" rx="24" transform="rotate(45 119 119)" fill="#8a7c6e"/>
</svg>
<div class="member-text" style="left:340px;top:2446px">
  <h3 class="member-name">Evan Park</h3>
  <p class="member-role">Principal</p>
  <p class="body-copy">Evan Park is a seasoned real estate expert with extensive experience in project and construction management, and a licensed real estate agent in California. Fluent in both English and Korean,...</p>
</div>

<svg class="abs" style="left:616px;top:2433px" width="238" height="238" role="img" aria-label="Portrait photo of Rafael Moreno">
  <rect x="40" y="40" width="158" height="158" rx="24" transform="rotate(45 119 119)" fill="#9fb3c4"/>
</svg>
<div class="member-text" style="left:882px;top:2446px">
  <h3 class="member-name">Rafael Moreno</h3>
  <p class="member-role">Principal</p>
  <p class="body-copy">Rafael Moreno brings almost 20 years of rich experience as a real estate investor and a pivotal role at one of southern California's largest real estate management firms, where he..</p>
</div>

<!-- Contact -->
<h2 class="section-title contact-title" style="top:2872px">Contact Us</h2>
<div class="rule" style="left:546px;top:2938px;background:var(--white)"></div>

<svg class="abs" style="left:350px;top:3037px" width="778" height="446" aria-hidden="true">
  <path d="M0 0 H708 A70 70 0 0 1 778 70 V376 A70 70 0 0 1 708 446 H0 Z" fill="var(--white)"/>
</svg>
<svg class="abs" style="left:74px;top:3004px" width="514" height="514" aria-hidden="true">
  <rect x="76" y="76" width="362" height="362" rx="56" transform="rotate(45 257 257)" fill="var(--navy)"/>
</svg>
<h3 class="addr-item addr-heading">Address</h3>
<div class="addr-item addr-brand"><span class="brand-dot"></span>Tollbrook Advisory</div>
<p class="addr-item addr-lines">418 Meridian Ave, Irvine,<br>CA 92614</p>
<a class="addr-item addr-link">Map Direction</a>

<h3 class="quick-title">Quick Contact</h3>
<div class="field" style="left:616px;top:3144px;width:238px">Name</div>
<div class="field" style="left:863px;top:3144px;width:239px">Email Address</div>
<div class="field" style="left:616px;top:3204px;width:238px">Phone No</div>
<div class="field" style="left:863px;top:3204px;width:239px">Subject</div>
<div class="field msg" style="left:616px;top:3264px;width:486px">Message</div>
<a class="btn submit">Submit</a>

<!-- Footer -->
<div class="footer-rule"></div>
<p class="copyright">Copyright © 2024 Company Name  All rights reserved.</p>
<div class="social" aria-label="Social media links">
  <span></span><span></span><span></span><span></span><span></span>
</div>

</body>
</html>
```